Brell Stone Company Business Cards

Front and Back Business Card - logo and text setup - cool design. I need workable photoshop or illustrator files so I can setup each employee card with design that is created
Updates

Hi everyone, thank you for the great entries. Please no more white and blue cards - there are so many already - black and silver only now please. thanks!

Target Market(s)

Construction Industry - Facility Managers

Industry/Entity Type

Construction

Contact Information for Business Card

I really like contemporary simplistic looks - clean neat....not opposed to seeing some black backrounds

Requirements
Must have
• Logo/website address with design on front only - www.brellstone-example.com (logo attached)
• Back:
• Name/Title/Company Address/Phone/email address
Nice to have
• Cool design
Should not have
• Nothing gimmicky like Fire or Water - since we are a Fire Protection company - it has all been done

```html
<!DOCTYPE html>
<html lang="en">
<head>
<meta charset="utf-8">
<title>Brell Stone Company – Business Cards</title>
<link rel="stylesheet" href="https://fonts.googleapis.com/css2?family=Lato:wght@400;700;900&display=swap">
<style>
  :root {
    --backdrop: #141414;
    --card: #222222;
    --card-edge: #2b2b2b;
    --ink: #f2f2f2;
    --accent: #e8452f;
    --rule: #cfcfcf;
  }
  * { box-sizing: border-box; margin: 0; padding: 0; }
  html, body {
    width: 1200px;
    height: 912px;
    overflow: hidden;
    background: var(--backdrop);
    font-family: "Lato", sans-serif;
    color: var(--ink);
  }
  .canvas {
    position: relative;
    width: 1200px;
    height: 912px;
  }
  .card {
    position: absolute;
    width: 640px;
    height: 366px;
    background: var(--card);
    border: 1px solid var(--card-edge);
    box-shadow: 0 18px 40px rgba(0, 0, 0, 0.55);
  }
  .card--front { left: 90px; top: 70px; }
  .card--back { left: 470px; top: 476px; }

  .wordmark {
    display: flex;
    align-items: center;
    gap: 12px;
    font-weight: 900;
    color: var(--accent);
    letter-spacing: -0.5px;
    line-height: 1;
  }
  .wordmark__mark {
    width: 0.55em;
    height: 0.55em;
    background: var(--accent);
  }
  .card--front .wordmark {
    position: absolute;
    left: 0; right: 0;
    top: 130px;
    justify-content: center;
    font-size: 62px;
  }
  .card--front .website {
    position: absolute;
    left: 0; right: 0;
    top: 250px;
    text-align: center;
    font-size: 17px;
    letter-spacing: 0.5px;
  }

  .card--back .wordmark {
    position: absolute;
    left: 40px;
    top: 236px;
    font-size: 40px;
  }
  .divider {
    position: absolute;
    left: 330px;
    top: 70px;
    width: 1px;
    height: 220px;
    background: var(--rule);
  }
  .contact {
    position: absolute;
    left: 356px;
    top: 76px;
    width: 270px;
  }
  .contact__name {
    font-size: 24px;
    font-weight: 700;
    color: var(--accent);
  }
  .contact__title {
    font-size: 15px;
    margin-top: 4px;
  }
  .contact__address {
    font-size: 15px;
    line-height: 1.35;
    margin-top: 18px;
    font-style: normal;
  }
  .contact__lines {
    list-style: none;
    margin-top: 16px;
    font-size: 15px;
  }
  .contact__lines li {
    display: flex;
    align-items: center;
    gap: 10px;
    line-height: 1.5;
  }
  .contact__lines svg {
    width: 14px;
    height: 14px;
    flex: none;
    fill: var(--accent);
  }
</style>
</head>
<body>
<main class="canvas">
  <section class="card card--front" aria-label="Card front">
    <div class="wordmark"><span class="wordmark__mark"></span><span>brellstone</span></div>
    <p class="website">www.brellstone-example.com</p>
  </section>

  <section class="card card--back" aria-label="Card back">
    <div class="wordmark"><span class="wordmark__mark"></span><span>brellstone</span></div>
    <div class="divider"></div>
    <div class="contact">
      <p class="contact__name">Dana Mercer Holt</p>
      <p class="contact__title">President</p>
      <address class="contact__address">48 Harbor Point Road<br>Lakeview Falls, NY 11900</address>
      <ul class="contact__lines">
        <li>
          <svg viewBox="0 0 24 24" aria-hidden="true"><path d="M6.6 10.8a15.1 15.1 0 0 0 6.6 6.6l2.2-2.2a1 1 0 0 1 1-.25 11.4 11.4 0 0 0 3.6.57 1 1 0 0 1 1 1V20a1 1 0 0 1-1 1A17 17 0 0 1 3 4a1 1 0 0 1 1-1h3.5a1 1 0 0 1 1 1c0 1.25.2 2.45.57 3.57a1 1 0 0 1-.25 1z"/></svg>
          <span>(555) 014-2290</span>
        </li>
        <li>
          <svg viewBox="0 0 24 24" aria-hidden="true"><path d="M2 5h20v14H2z M4 7v.5l8 5 8-5V7z" fill-rule="evenodd"/></svg>
          <span>info@brellstone-example.com</span>
        </li>
        <li>
          <svg viewBox="0 0 24 24" aria-hidden="true"><path d="M12 2a10 10 0 1 0 0 20 10 10 0 0 0 0-20zm6.9 9h-3a15 15 0 0 0-1.3-6A8 8 0 0 1 18.9 11zM12 4.1c.9 1.3 1.7 3.6 1.9 6.9h-3.8c.2-3.3 1-5.6 1.9-6.9zM9.4 5a15 15 0 0 0-1.3 6h-3A8 8 0 0 1 9.4 5zM5.1 13h3a15 15 0 0 0 1.3 6A8 8 0 0 1 5.1 13zm6.9 6.9c-.9-1.3-1.7-3.6-1.9-6.9h3.8c-.2 3.3-1 5.6-1.9 6.9zm2.6-.9a15 15 0 0 0 1.3-6h3a8 8 0 0 1-4.3 6z"/></svg>
          <span>www.brellstone-example.com</span>
        </li>
      </ul>
    </div>
  </section>
</main>
</body>
</html>
```